Employee Benefits and Insurance Consulting

We are an existing company with over 30 years experience but are changing our name. We would like a simple design with grey tones.

Industry/Entity Type

Insurance

Contact Information for Business Card

Marlow Benefits Consulting
Gerald P Hollins CEO
5172 Brackenridge Road
Louisville, TN 37777
gerald@marlowbenefits-example.com
865-412-5593 - O
865-247-3861 - C

```html
<!DOCTYPE html>
<html lang="en">
<head>
<meta charset="utf-8">
<title>Marlow Benefits Consulting – Business Card</title>
<link rel="stylesheet" href="https://fonts.googleapis.com/css2?family=Arimo:ital,wght@0,400;0,700;1,400&display=swap">
<style>
  :root {
    --backdrop: #e6e6e6;
    --card-white: #ffffff;
    --swoosh-dark: #5f6163;
    --swoosh-light: #b9bbbd;
    --panel-top: #d9dadb;
    --panel-bottom: #b4b6b8;
    --footer-band: #9c9ea0;
    --ink: #262626;
    --ink-soft: #555555;
    --ink-muted: #7a7a7a;
    --footer-text: #ffffff;
  }
  html, body {
    margin: 0;
    width: 1200px;
    height: 799px;
    overflow: hidden;
    background: var(--backdrop);
  }
  .business-card {
    position: absolute;
    left: 110px;
    top: 120px;
    width: 980px;
    height: 560px;
    box-shadow: 0 10px 30px rgba(0,0,0,0.18);
    font-family: "Arimo", Arial, sans-serif;
    overflow: hidden;
  }
  .card-art { position: absolute; inset: 0; }
  .brand {
    position: absolute;
    left: 52px;
    top: 98px;
    display: flex;
    align-items: center;
    gap: 14px;
  }
  .brand-dot {
    width: 22px;
    height: 22px;
    border-radius: 50%;
    background: var(--ink);
  }
  .brand-name {
    font-size: 31px;
    font-weight: 400;
    color: var(--ink);
    letter-spacing: 0.5px;
  }
  .holder {
    position: absolute;
    left: 640px;
    top: 140px;
    width: 300px;
    text-align: center;
  }
  .holder-name {
    font-size: 33px;
    font-weight: 400;
    color: var(--ink);
    margin: 0;
  }
  .holder-title {
    font-size: 17px;
    font-style: italic;
    color: var(--ink-muted);
    margin: 6px 0 0;
  }
  .contact-list {
    position: absolute;
    left: 700px;
    top: 290px;
    margin: 0;
    padding: 0;
    list-style: none;
    font-size: 17px;
    color: var(--ink-soft);
  }
  .contact-list li {
    display: flex;
    align-items: center;
    gap: 10px;
    height: 30px;
  }
  .contact-icon { width: 20px; height: 20px; }
  .address {
    position: absolute;
    left: 700px;
    top: 385px;
    font-size: 16px;
    line-height: 27px;
    color: var(--ink-soft);
    font-style: normal;
  }
  .email {
    position: absolute;
    left: 0;
    width: 860px;
    top: 508px;
    text-align: center;
    font-size: 21px;
    color: var(--footer-text);
  }
</style>
</head>
<body>
  <article class="business-card">
    <svg class="card-art" viewBox="0 0 980 560" width="980" height="560" aria-hidden="true">
      <defs>
        <linearGradient id="panel-gradient" x1="0" y1="0" x2="0.3" y2="1">
          <stop offset="0" stop-color="var(--panel-top)"/>
          <stop offset="1" stop-color="var(--panel-bottom)"/>
        </linearGradient>
      </defs>
      <rect class="panel" width="980" height="560" fill="url(#panel-gradient)"/>
      <path class="swoosh-light" d="M650,0 H700 C610,210 440,440 0,470 V450 C420,410 570,200 650,0 Z" fill="var(--swoosh-light)"/>
      <path class="swoosh-dark" d="M600,0 H652 C570,200 420,410 0,450 V425 C380,380 520,170 600,0 Z" fill="var(--swoosh-dark)"/>
      <path class="white-field" d="M0,0 H602 C522,170 382,380 0,427 Z" fill="var(--card-white)"/>
      <rect class="footer-band" y="490" width="980" height="70" fill="var(--footer-band)" opacity="0.55"/>
    </svg>

    <div class="brand">
      <span class="brand-dot"></span>
      <span class="brand-name">Marlow Benefits Consulting</span>
    </div>

    <div class="holder">
      <h1 class="holder-name">Gerald P Hollins</h1>
      <p class="holder-title">(CEO)</p>
    </div>

    <ul class="contact-list">
      <li>
        <svg class="contact-icon" viewBox="0 0 20 20" aria-label="Cell">
          <circle cx="10" cy="10" r="9" fill="none" stroke="var(--ink)" stroke-width="1.6"/>
          <rect x="7" y="4.5" width="6" height="11" rx="1.2" fill="var(--ink)"/>
          <rect x="8" y="6" width="4" height="7" fill="var(--card-white)"/>
        </svg>
        <span>865-247-3861</span>
      </li>
      <li>
        <svg class="contact-icon" viewBox="0 0 20 20" aria-label="Office">
          <circle cx="10" cy="10" r="9.5" fill="var(--ink)"/>
          <path d="M6.3,5.2 L8.2,5 L9,7.6 L7.8,8.6 C8.5,10.1 9.7,11.3 11.3,12.1 L12.3,10.9 L14.9,11.7 L14.7,13.7 C10,14 5.9,10 6.3,5.2 Z" fill="var(--card-white)"/>
        </svg>
        <span>865-412-5593</span>
      </li>
    </ul>

    <address class="address">
      5172 Brackenridge Road<br>
      Louisville, TN 37777
    </address>

    <p class="email">gerald@marlowbenefits-example.com</p>
  </article>
</body>
</html>
```